Velvet Glow Co. Derma Roller packaging design

I need a box designed for a skin care brand called Velvet Glow Co. The box will be for our Derma Roller- a skin rejuvenation device. It will be sold online with lots of competition. I would like a modern, high end design, something that stands out and looks amazing. My logo is blush pink and black, for packaging i need no more than 3 colours, maybe gold if any other colour is used. A photo of a sample derma roller is attached below for an idea of what the product looks like, however my roller with have a clear handle with a black roller. The roller comes in a clear case, the box dimensions will need to be 16 cm long, 4 cm high, 4.5 cm wide.
ATTACHED ARE 2 SAMPLE BOXES AS AN EXAMPLE OF THE SIZE OF BOX REQUIRED!

Target Market(s)

25-50 year old women in the US

Colors
e667a6
000000
efefef

Requirements
Must have
• LOGO
• NAME OF PRODUCT- Cosmetic Derma Roller
• NEEDLE DEPTH- 0.25mm
• CAUTION- For personal use only, Do not use if allergic to metal, Do not use on open skin, wounds or active acne, sterilise roller before and after use.
Nice to have
• BENEFITS- Skin Rejuvenation, Collagen Induction Therapy, Increase product absorption, reduce acne scars and pigmentation
• FEATURES- 540 high quality titanium needles, ultra sharp needle tips, cross-line needle arrangement, ergonomic handle, anti slip grip,

```html
<!DOCTYPE html>
<html lang="en">
<head>
<meta charset="utf-8">
<title>Velvet Glow Co. – Cosmetic Derma Roller Packaging</title>
<link href="https://fonts.googleapis.com/css2?family=Oswald:wght@400;500&display=swap" rel="stylesheet">
<style>
  :root {
    --page-bg: #f8f2f0;
    --marble-light: #f6d5ce;
    --marble-mid: #eecac2;
    --marble-vein: #b89d9b;
    --rose-gold-light: #f3d3c3;
    --rose-gold: #d7a48c;
    --rose-gold-dark: #c08a74;
    --label-white: #ffffff;
    --ink: #1c1a1a;
  }
  * { box-sizing: border-box; margin: 0; padding: 0; }
  html, body {
    width: 1200px;
    height: 1200px;
    overflow: hidden;
    background: var(--page-bg);
  }
  .canvas {
    position: relative;
    width: 1200px;
    height: 1200px;
    font-family: "Oswald", sans-serif;
  }
  .box-face {
    position: absolute;
    top: 62px;
    width: 400px;
    height: 1076px;
    box-shadow: 0 4px 14px rgba(90, 60, 55, 0.25);
  }
  .box-face--front { left: 134px; }
  .box-face--back { left: 666px; }
  .marble {
    position: absolute;
    inset: 0;
    background:
      radial-gradient(ellipse 60% 18% at 40% 22%, rgba(184,157,155,0.35), transparent 70%),
      radial-gradient(ellipse 50% 20% at 60% 82%, rgba(184,157,155,0.35), transparent 70%),
      radial-gradient(ellipse 70% 40% at 30% 60%, rgba(255,240,236,0.6), transparent 70%),
      linear-gradient(160deg, var(--marble-light), var(--marble-mid) 50%, var(--marble-light));
  }
  .label-frame {
    position: absolute;
    left: 24px;
    width: 355px;
    padding: 12px;
    background: linear-gradient(120deg, var(--rose-gold-dark), var(--rose-gold-light) 35%, var(--rose-gold) 60%, var(--rose-gold-light) 85%, var(--rose-gold-dark));
  }
  .box-face--front .label-frame { top: 358px; height: 358px; }
  .box-face--back .label-frame { top: 360px; height: 360px; }
  .label {
    width: 100%;
    height: 100%;
    background: var(--label-white);
    position: relative;
  }
  .brand-lockup {
    position: absolute;
    top: 92px;
    left: 0;
    right: 0;
    display: flex;
    align-items: center;
    justify-content: center;
    gap: 10px;
  }
  .brand-mark {
    width: 14px;
    height: 14px;
    background: #e8b7bf;
  }
  .brand-name {
    font-size: 26px;
    font-weight: 400;
    letter-spacing: 3px;
    color: var(--ink);
    text-transform: uppercase;
  }
  .product-title {
    font-size: 24px;
    font-weight: 500;
    color: var(--rose-gold);
    text-align: center;
    letter-spacing: 0.3px;
  }
  .box-face--front .product-title {
    position: absolute;
    top: 258px;
    left: 0;
    right: 0;
  }
  .box-face--back .product-title { padding-top: 44px; }
  .spec-list {
    padding: 22px 22px 0 26px;
  }
  .spec {
    font-size: 11.6px;
    font-weight: 400;
    line-height: 19.2px;
    color: var(--ink);
    text-transform: uppercase;
    margin-bottom: 19px;
  }
</style>
</head>
<body>
<main class="canvas">
  <section class="box-face box-face--front" aria-label="Front panel">
    <div class="marble" role="img" aria-label="Blush pink marble texture with grey veining"></div>
    <div class="label-frame">
      <div class="label">
        <div class="brand-lockup">
          <span class="brand-mark"></span>
          <span class="brand-name">Velvet Glow Co.</span>
        </div>
        <h1 class="product-title">COSMETIC DERMA ROLLER</h1>
      </div>
    </div>
  </section>

  <section class="box-face box-face--back" aria-label="Back panel">
    <div class="marble" role="img" aria-label="Blush pink marble texture with grey veining"></div>
    <div class="label-frame">
      <div class="label">
        <h2 class="product-title">COSMETIC DERMA ROLLER</h2>
        <div class="spec-list">
          <p class="spec">Benefits: skin rejuvenation, collagen induction therapy, increase product absorption, reduce acne scars and pigmentation</p>
          <p class="spec">Features: 540 high quality 0.25 mm titanium needles, ultra sharp needle tips, cross-line needle arrangement, ergonomic handle, anti slip grip</p>
          <p class="spec">Caution: for personal use only, do not use if allergic to metal, do not use on open skin, wounds or active acne, sterilise roller before and after use.</p>
        </div>
      </div>
    </div>
  </section>
</main>
</body>
</html>
```